Oil Field Service company needs professional business cards

Looking to clean up our current company business cards and look a little more professional. Brenwick Casing Services is a US based company that services the oil field. We deal with engineers, managers and oil rigs....................................................................................................................................................................................................................................................................................................................................................................................................

Target Market(s)

Oil and Gas professionals

Industry/Entity Type

Oil And Gas

Contact Information for Business Card

See attached photo as example

Font styles to use
Sans Serif

Colors
ec1f27

Requirements
Must have
• Company Logo, Name, Title, Cell, Office, Fax, Email.
• See attached photo
Nice to have
• External CRT, Internal CRT, Casing Crews, Torque Turn, Laydown Machine
Should not have
• Do not introduce any new pictures and keep it professional looking

```html
<!DOCTYPE html>
<html lang="en">
<head>
<meta charset="utf-8">
<title>Brenwick Casing Services – Business Card</title>
<link href="https://fonts.googleapis.com/css2?family=Source+Sans+3:wght@400;600;700&display=swap" rel="stylesheet">
<style>
  :root {
    --stage: #161616;
    --card-light: #f3f3f3;
    --brand-red: #e31e26;
    --slate: #3b4650;
    --ink: #1c1c1c;
    --white: #ffffff;
  }
  * { margin: 0; padding: 0; box-sizing: border-box; }
  html, body {
    width: 1200px;
    height: 900px;
    overflow: hidden;
    background: var(--stage);
    font-family: "Source Sans 3", "Helvetica Neue", Arial, sans-serif;
  }
  .canvas {
    position: relative;
    width: 1200px;
    height: 900px;
  }
  .card {
    position: absolute;
    top: 184px;
    height: 490px;
    border-radius: 12px;
    text-align: center;
  }
  .card--front {
    left: 299px;
    width: 301px;
    background: var(--card-light);
    color: var(--ink);
  }
  .card--back {
    left: 645px;
    width: 305px;
    background: var(--brand-red);
  }
  .wordmark {
    font-weight: 700;
    letter-spacing: 0.06em;
    line-height: 1;
  }
  .wordmark__name {
    display: block;
    font-size: 40px;
  }
  .wordmark__sub {
    display: block;
    font-size: 14px;
    letter-spacing: 0.22em;
    margin-top: 12px;
  }
  .card--front .wordmark {
    position: absolute;
    top: 104px;
    left: 0;
    right: 0;
    color: var(--slate);
  }
  .card--back .wordmark {
    position: absolute;
    top: 366px;
    left: 0;
    right: 0;
    color: var(--white);
  }
  .person {
    position: absolute;
    top: 242px;
    left: 0;
    right: 0;
  }
  .person__name {
    font-size: 17px;
    font-weight: 600;
    color: var(--brand-red);
    line-height: 20px;
  }
  .person__title {
    font-size: 13.5px;
    line-height: 17px;
  }
  .contact {
    position: absolute;
    top: 306px;
    left: 0;
    right: 0;
    list-style: none;
    font-size: 13.5px;
    line-height: 17.6px;
  }
  .services {
    position: absolute;
    top: 400px;
    left: 0;
    right: 0;
    font-size: 13.5px;
    line-height: 17.6px;
  }
</style>
</head>
<body>
  <main class="canvas">
    <section class="card card--front" aria-label="Business card front">
      <div class="wordmark">
        <span class="wordmark__name">BRENWICK</span>
        <span class="wordmark__sub">CASING SERVICES</span>
      </div>
      <div class="person">
        <p class="person__name">Cody Marlow</p>
        <p class="person__title">Area Manager</p>
      </div>
      <ul class="contact">
        <li>(555) 418-2093</li>
        <li>(555) 672-1845</li>
        <li>(555) 903-5561</li>
        <li>cody.marlow@brenwickcasing.com</li>
      </ul>
      <div class="services">
        <p>Laydown Machine | Casing Crew</p>
        <p>Mud Tool | Torque Turn</p>
      </div>
    </section>

    <section class="card card--back" aria-label="Business card back">
      <div class="wordmark">
        <span class="wordmark__name">BRENWICK</span>
        <span class="wordmark__sub">CASING SERVICES</span>
      </div>
    </section>
  </main>
</body>
</html>
```